Store Front Sign for Vape Store

Interested in getting a store front sign graphic done. Sign is for over the door (lighted sign). Dimensions of sign: 6 feet long x 2 feet high.
Sign is for a Vape Store. I have attached the logo to be used.
Looking for a modern and professional look
Phone numbers to be used.
Whatsapp# 394-6150
Contact #562-7038
Sign should have Instagram & Facebook logos and. handle @lumoramists

Industry/Entity Type

Vape | Electronic Cigarettes

Colors

Designer to choose colors to be used in the design.

Requirements
Must have
• Facebook and Instagram Logos. Contact Numbers.
Should not have
• Any Persons.

```html
<!DOCTYPE html>
<html lang="en">
<head>
<meta charset="utf-8">
<title>Lumora Mists – Storefront Sign</title>
<link rel="stylesheet" href="https://fonts.googleapis.com/css2?family=Anton&family=Oswald:wght@300;600&family=Poppins:wght@400;500&display=swap">
<style>
  :root {
    --backdrop: #b9b9b9;
    --sign-dark: #1e1e20;
    --sign-mid: #3a3a3e;
    --vape-blue: #10a9e8;
    --vape-blue-light: #5fd0fb;
    --text-white: #ffffff;
    --divider: #5a5a5e;
  }
  * { margin: 0; padding: 0; box-sizing: border-box; }
  html, body {
    width: 1031px; height: 1200px; overflow: hidden;
    background: var(--backdrop);
  }
  .sign {
    position: absolute; left: 61px; top: 780px;
    width: 910px; height: 303px;
    background: radial-gradient(ellipse at 45% 50%, var(--sign-mid) 0%, var(--sign-dark) 70%);
    box-shadow: 6px 8px 10px rgba(0,0,0,0.35);
    overflow: hidden;
  }
  .smoke-texture {
    position: absolute; right: 0; top: 0; width: 150px; height: 100%;
    background: linear-gradient(90deg, rgba(141,141,147,0) 0%, rgba(141,141,147,0.4) 55%, rgba(190,190,196,0.65) 100%);
  }
  .smoke-texture.low-left {
    left: 0; right: auto; top: auto; bottom: 0; width: 140px; height: 60px;
    background: radial-gradient(ellipse at 10% 100%, rgba(141,141,147,0.45) 0%, rgba(141,141,147,0) 70%);
  }
  .headline {
    position: absolute; left: 52px; top: 52px;
    font-family: "Anton", "Impact", sans-serif;
    font-size: 111px; line-height: 1; letter-spacing: 7px;
    transform: scaleX(1.3); transform-origin: left top;
    background: linear-gradient(160deg, var(--vape-blue) 0%, var(--vape-blue-light) 45%, var(--vape-blue) 70%);
    -webkit-background-clip: text; background-clip: text; color: transparent;
    white-space: nowrap;
  }
  .tagline {
    position: absolute; left: 52px; top: 166px;
    font-family: "Oswald", sans-serif; font-size: 40px; line-height: 1;
    letter-spacing: 8.5px; color: var(--text-white); white-space: nowrap;
  }
  .tagline .light { font-weight: 300; }
  .tagline .bold { font-weight: 600; margin-left: 8px; }
  .contact-row {
    position: absolute; left: 52px; top: 238px;
    display: flex; align-items: center; gap: 16px;
    font-family: "Poppins", sans-serif; color: var(--text-white);
    font-size: 15px; white-space: nowrap;
  }
  .contact-item { display: flex; align-items: center; gap: 4px; }
  .contact-item svg { width: 13px; height: 13px; }
  .divider { width: 1px; height: 20px; background: var(--divider); }
  .follow { display: flex; align-items: center; gap: 6px; font-size: 11px; }
  .follow .handle { font-size: 15px; }
  .social-dot { width: 18px; height: 18px; border-radius: 50%; background: var(--vape-blue); }
  .brand-badge {
    position: absolute; left: 727px; top: 60px;
    width: 144px; height: 144px; border-radius: 50%;
    background: var(--sign-dark);
    border: 3px solid var(--vape-blue);
    box-shadow: 0 0 0 6px #151517;
    display: flex; align-items: center; justify-content: center;
  }
  .brand-name {
    font-family: "Poppins", sans-serif; font-weight: 500;
    font-size: 20px; line-height: 1.15; text-align: center;
    color: var(--text-white);
  }
</style>
</head>
<body>
  <div class="sign">
    <div class="smoke-texture" role="img" aria-label="Soft grey smoke wisps drifting along the right edge"></div>
    <div class="smoke-texture low-left" role="img" aria-label="Faint smoke wisp in the lower left corner"></div>

    <div class="headline">VAPE SHOP</div>
    <div class="tagline"><span class="light">STOP SMOKING</span><span class="bold">START VAPING</span></div>

    <div class="contact-row">
      <div class="contact-item">
        <svg viewBox="0 0 24 24" aria-hidden="true"><path fill="#10a9e8" d="M6.6 10.8a15.1 15.1 0 0 0 6.6 6.6l2.2-2.2a1 1 0 0 1 1-.25 11.4 11.4 0 0 0 3.6.57 1 1 0 0 1 1 1V20a1 1 0 0 1-1 1A17 17 0 0 1 3 4a1 1 0 0 1 1-1h3.5a1 1 0 0 1 1 1c0 1.25.2 2.45.57 3.57a1 1 0 0 1-.25 1z"/></svg>
        <span>394-6150 · 562-7038</span>
      </div>
      <div class="contact-item">
        <svg viewBox="0 0 24 24" aria-hidden="true"><g fill="none" stroke="#10a9e8" stroke-width="2"><circle cx="12" cy="12" r="9"/><ellipse cx="12" cy="12" rx="4" ry="9"/><path d="M3 12h18M5 7h14M5 17h14"/></g></svg>
        <span>lumoramists.shop</span>
      </div>
      <div class="divider"></div>
      <div class="follow">
        <span>Follow us on</span>
        <span class="social-dot"></span>
        <span class="social-dot"></span>
        <span class="handle">@lumoramists</span>
      </div>
    </div>

    <div class="brand-badge">
      <span class="brand-name">Lumora<br>Mists</span>
    </div>
  </div>
</body>
</html>
```